Construction material supplies company business card ****

1. Full company name “K T Masonry Works Ltd”
I am after a Business card design for the company as a whole. We are better known in Solomon Islands as “K T Masonry” for short.

We are a building materials supplier of
Ready Mixed Concrete, Bricks and Blocks,
Quarry products- gravel, aggregates, sand etc.
Cement distributor/retailer of reputable brands.
Other prefab concrete products. Culverts, wave breakers, concrete retaining blocks etc.

2. Competitive Advantage over Competition: Quality, efficient, professional, dependable, reliable

3. We want people to feel trust worthy, high quality, strong when they see our brand

5. No preference to color. Maybe more sturdy and corporate. Not fancy.

Industry/Entity Type

CONSTRUCTION SUPPLY

Contact Information for Business Card

Name, Position, office phone mob phone, email

Requirements
Must have
• the company logo
Nice to have
• would like to see a mixture of designs, of with logo only and also with simple graphic designs to bring out the company whilst still have the strong sturdy professional feeling

```html
<!DOCTYPE html>
<html lang="en">
<head>
<meta charset="utf-8">
<title>K T Masonry – Business Card</title>
<link href="https://fonts.googleapis.com/css2?family=Roboto:wght@400;500;700&display=swap" rel="stylesheet">
<style>
  :root {
    --backdrop: #2a2a2a;
    --navy: #1d3f66;
    --navy-deep: #132d4d;
    --blue-mid: #2c5580;
    --blue-light: #3a6690;
    --stone: #e4e4e2;
    --stone-dark: #cfcfcc;
    --white: #ffffff;
    --ink-soft: #eef2f7;
  }
  * { box-sizing: border-box; margin: 0; padding: 0; }
  html, body { width: 1200px; height: 1138px; overflow: hidden; }
  body {
    background: var(--backdrop);
    font-family: "Roboto", Arial, sans-serif;
    position: relative;
  }
  .card {
    position: absolute;
    left: 275px;
    width: 622px;
    height: 375px;
    border-radius: 16px;
    overflow: hidden;
  }
  /* Front */
  .card--front {
    top: 186px;
    background: linear-gradient(160deg, var(--blue-light) 0%, var(--blue-mid) 45%, var(--navy) 100%);
    color: var(--ink-soft);
  }
  .brand {
    position: absolute;
    display: flex;
    align-items: center;
    gap: 14px;
    font-weight: 500;
    letter-spacing: 2px;
    white-space: nowrap;
  }
  .brand__mark {
    display: block;
    border: 5px solid currentColor;
  }
  .card--front .brand {
    left: 0; right: 0; top: 64px;
    justify-content: center;
    color: var(--white);
    font-size: 54px;
  }
  .card--front .brand__mark { width: 52px; height: 52px; }
  .intro-pill {
    position: absolute;
    left: 138px; top: 186px;
    width: 347px; height: 40px;
    border-radius: 20px;
    background: var(--blue-mid);
    border: 1px solid rgba(255,255,255,0.12);
    display: flex; align-items: center; justify-content: center;
    font-size: 16px;
    z-index: 2;
  }
  .product-band {
    position: absolute;
    left: 0; right: 0; top: 214px; height: 78px;
    background: rgba(15, 40, 72, 0.75);
    padding-top: 23px;
    text-align: center;
    font-size: 16px;
    line-height: 22px;
  }
  .product-extra {
    position: absolute;
    left: 0; right: 0; top: 305px;
    text-align: center;
    font-size: 16px;
    line-height: 25px;
  }
  /* Back */
  .card--back {
    top: 608px;
    background: radial-gradient(ellipse at 40% 30%, #ececea 0%, var(--stone) 55%, var(--stone-dark) 100%);
    color: var(--navy);
  }
  .card--back .brand {
    right: 34px; top: 52px;
    font-size: 38px;
    gap: 10px;
  }
  .card--back .brand__mark { width: 36px; height: 36px; border-width: 4px; }
  .person { position: absolute; left: 30px; top: 190px; }
  .person__name { font-size: 23px; font-weight: 500; line-height: 26px; }
  .person__role { font-size: 16px; line-height: 22px; margin-top: 2px; }
  .divider { position: absolute; left: 0; top: 0; }
  .contacts {
    position: absolute; left: 30px; top: 272px;
    list-style: none;
    font-size: 17px;
    line-height: 26px;
  }
  .contacts li { display: flex; align-items: center; gap: 14px; }
  .contacts svg { width: 16px; height: 16px; fill: var(--navy); }
  .address {
    position: absolute; right: 34px; top: 294px;
    text-align: right;
    font-size: 17px;
    line-height: 26px;
    font-style: normal;
  }
</style>
</head>
<body>

<section class="card card--front">
  <div class="brand"><span class="brand__mark"></span>K T MASONRY</div>
  <div class="intro-pill">We are a building materials supplier of</div>
  <div class="product-band">
    Ready Mixed Concrete, Bricks and Blocks, Quarry Products<br>
    Quarry Products:- Gravel, Aggregates, Sand Etc.
  </div>
  <div class="product-extra">
    Cement Distributor/Retailer of Reputable Brands.<br>
    Other Concrete Products Culverts, Wave Breakers, Concrete Retaining Blocks
  </div>
</section>

<section class="card card--back">
  <div class="brand"><span class="brand__mark"></span>K T MASONRY</div>
  <div class="person">
    <p class="person__name">Peter Walsh</p>
    <p class="person__role">Managing Director</p>
  </div>
  <svg class="divider" width="622" height="375" viewBox="0 0 622 375" aria-hidden="true">
    <path d="M30 255 H310 C335 255 340 274 368 274 H588" fill="none" stroke="#1d3f66" stroke-width="1.5"/>
  </svg>
  <ul class="contacts">
    <li>
      <svg viewBox="0 0 16 16"><path d="M2 6c0-2 2-3 6-3s6 1 6 3v1h-3V5.5H5V7H2zM4 8h8l1 5H3z"/></svg>
      000 0000 0000
    </li>
    <li>
      <svg viewBox="0 0 16 16"><path d="M1 3h14v10H1zM2.5 4.5 8 9l5.5-4.5v1L8 10 2.5 5.5z" fill-rule="evenodd"/></svg>
      peter@ktmasonry.com
    </li>
    <li>
      <svg viewBox="0 0 16 16"><path d="M8 1a7 7 0 1 0 0 14A7 7 0 0 0 8 1zm0 1.5c.8 0 1.8 1.8 2 4.5H6c.2-2.7 1.2-4.5 2-4.5zM2.6 7a5.5 5.5 0 0 1 2.5-4C4.6 4 4.3 5.4 4.3 7zm0 2h1.7c0 1.6.3 3 .8 4a5.5 5.5 0 0 1-2.5-4zM8 13.5c-.8 0-1.8-1.8-2-4.5h4c-.2 2.7-1.2 4.5-2 4.5zM10.9 13c.5-1 .8-2.4.8-4h1.7a5.5 5.5 0 0 1-2.5 4zm.8-6c0-1.6-.3-3-.8-4a5.5 5.5 0 0 1 2.5 4z"/></svg>
      www.ktmasonry.com
    </li>
  </ul>
  <address class="address">
    234 Anywhere St., Any City,<br>
    Any Town, US 123456
  </address>
</section>

</body>
</html>
```